Whitcombe Business Card Design

The name of the business is Dario Whitcombe, CPA LLC
The service that we offer is Accounting, Tax & Consulting Services. I need it to have the following items:
Dario Whitcombe, Principal
Phone Number
Email Address
Physical Address

I have attached the company logo, one in black and one in white. Please provide a design in black background and the other in white background. Please include "Accounting, Tax & Consulting Services". I want the business card to be clean and very professional.

```html
<!DOCTYPE html>
<html lang="en">
<head>
<meta charset="utf-8">
<title>Dario Whitcombe, CPA LLC — Business Card</title>
<link href="https://fonts.googleapis.com/css2?family=Montserrat:wght@500;600;700&family=Raleway:wght@400;500&family=Oswald:wght@500&display=swap" rel="stylesheet">
<style>
  :root {
    --backdrop: #d4d5d7;
    --card-light: #ffffff;
    --card-dark: #3b3b3d;
    --ink: #3a3a3c;
    --ink-soft: #4a4a4c;
    --accent: #9e1b1f;
    --band: #3b3b3d;
    --mark-grey: #8d8d90;
  }
  * { margin: 0; padding: 0; box-sizing: border-box; }
  html, body { width: 1015px; height: 1200px; overflow: hidden; background: var(--backdrop); }
  .canvas { position: relative; width: 1015px; height: 1200px; }

  .card { position: absolute; left: 82px; width: 822px; height: 469px; border-radius: 35px; overflow: hidden; }
  .card--front { top: 83px; background: var(--card-light); }
  .card--back { top: 603px; background: var(--card-dark); }

  /* Front: brand block */
  .brand { position: absolute; left: 40px; top: 170px; width: 340px; text-align: center; }
  .brand__square { width: 58px; height: 58px; background: var(--ink); margin: 0 auto 22px; }
  .brand__name { font-family: "Montserrat", sans-serif; font-weight: 600; font-size: 19px; color: var(--ink); white-space: nowrap; }

  .divider { position: absolute; left: 405px; top: 113px; width: 2px; height: 242px; background: var(--accent); }

  .person { position: absolute; left: 433px; top: 104px; }
  .person__name { font-family: "Montserrat", sans-serif; font-weight: 700; font-size: 39px; letter-spacing: -1px; color: var(--accent); line-height: 1; }
  .person__title { font-family: "Raleway", sans-serif; font-weight: 500; font-size: 22px; color: var(--ink-soft); margin-top: 8px; }

  .contacts { position: absolute; left: 436px; top: 188px; list-style: none; }
  .contacts li { display: flex; align-items: center; height: 32.5px; font-family: "Raleway", sans-serif; font-size: 21px; color: var(--ink-soft); }
  .contacts svg { width: 18px; height: 18px; margin-right: 24px; flex: none; }

  .address { position: absolute; left: 433px; top: 300px; font-family: "Raleway", sans-serif; font-size: 21px; line-height: 32px; color: var(--ink-soft); }

  .footer-band { position: absolute; left: 0; bottom: 0; width: 822px; height: 40px; }
  .footer-band__tagline { position: absolute; right: 24px; bottom: 6px; font-family: "Oswald", sans-serif; font-weight: 500; font-size: 18px; color: #fff; letter-spacing: 0.2px; }

  /* Back */
  .back-brand { position: absolute; left: 0; width: 822px; top: 112px; text-align: center; }
  .back-brand__square { width: 140px; height: 140px; background: #2c2c2e; margin: 0 auto 42px; }
  .back-brand__name { font-family: "Montserrat", sans-serif; font-weight: 600; font-size: 36px; color: var(--mark-grey); }
  .back-tagline { position: absolute; left: 0; width: 822px; top: 386px; text-align: center; font-family: "Montserrat", sans-serif; font-weight: 500; font-size: 21px; color: #fff; }
</style>
</head>
<body>
<main class="canvas">

  <section class="card card--front" aria-label="Business card front">
    <div class="brand">
      <div class="brand__square"></div>
      <p class="brand__name">DARIO WHITCOMBE, CPA, LLC</p>
    </div>

    <div class="divider"></div>

    <div class="person">
      <h1 class="person__name">NOLAN HARTWELL</h1>
      <p class="person__title">Managing Director</p>
    </div>

    <ul class="contacts">
      <li>
        <svg viewBox="0 0 24 24" aria-hidden="true"><path fill="#9e1b1f" d="M6.6 10.8c1.4 2.8 3.8 5.1 6.6 6.6l2.2-2.2c.3-.3.7-.4 1-.2 1.1.4 2.3.6 3.6.6.6 0 1 .4 1 1V20c0 .6-.4 1-1 1C10.6 21 3 13.4 3 4c0-.6.4-1 1-1h3.5c.6 0 1 .4 1 1 0 1.3.2 2.5.6 3.6.1.3 0 .7-.2 1z"/></svg>
        044-555 019 284
      </li>
      <li>
        <svg viewBox="0 0 24 24" aria-hidden="true"><path fill="#9e1b1f" d="M2 5h20v14H2z"/><path fill="none" stroke="#fff" stroke-width="1.6" d="M2 5l10 8 10-8"/></svg>
        info@whitcombecpa.com
      </li>
      <li>
        <svg viewBox="0 0 24 24" aria-hidden="true"><circle cx="12" cy="12" r="10" fill="#9e1b1f"/><path fill="none" stroke="#fff" stroke-width="1.4" d="M2 12h20M12 2c3 3 3 17 0 20M12 2c-3 3-3 17 0 20"/></svg>
        www.whitcombecpa.com
      </li>
    </ul>

    <p class="address">421, Address line here<br>Country Name, 45452</p>

    <div class="footer-band">
      <svg width="822" height="40" viewBox="0 0 822 40" aria-hidden="true">
        <rect x="0" y="29" width="822" height="11" fill="var(--band)"/>
        <polygon points="0,12 472,12 465,22 0,22" fill="var(--accent)"/>
        <polygon points="497,0 822,0 822,40 460,40" fill="var(--band)"/>
      </svg>
      <span class="footer-band__tagline">ACCOUNTING, TAX &amp; CONSULTING SERVICES</span>
    </div>
  </section>

  <section class="card card--back" aria-label="Business card back">
    <div class="back-brand">
      <div class="back-brand__square"></div>
      <p class="back-brand__name">DARIO WHITCOMBE, CPA, LLC</p>
    </div>
    <p class="back-tagline">Accounting, Tax &amp; Consulting Services</p>
  </section>

</main>
</body>
</html>
```